Tollen Ridge Canvas Camps

I am Moving from nest QiV and Qelt to host my own website to create direct bookings. I haves booking platform, I just need a website to embed it into. I want a catchy website to attract potential guests to book at my accommodation located near morvane national park in Alberta, Canada.

Here is my nest QiV links:
https://www.nestqiv.ca/rooms/2048613927465105319?viralityEntryPoint=1&s=76

https://www.nestqiv.ca/rooms/2093547718260493127?viralityEntryPoint=1&s=76

https://www.nestqiv.ca/rooms/2184736590218374662?viralityEntryPoint=1&s=76

https://www.nestqiv.ca/rooms/2065128834710952483?viralityEntryPoint=1&s=76

https://www.nestqiv.ca/rooms/2317465098321857704?viralityEntryPoint=1&s=76

```html
<!DOCTYPE html>
<html lang="en">
<head>
<meta charset="utf-8">
<title>Tollen Ridge Canvas Camps</title>
<link href="https://fonts.googleapis.com/css2?family=Cinzel:wght@600;700;800&family=Roboto:wght@400;500;700&family=Arimo:wght@400&display=swap" rel="stylesheet">
<style>
:root{
  --brown:#3b2920;
  --brown-deep:#2f2019;
  --ink:#1b1b1b;
  --muted:#555;
  --panel:#e6e6e6;
  --white:#fff;
  --grey-deco:#c9c9c9;
  --display:'Cinzel',serif;
  --body:'Roboto',sans-serif;
}
*{box-sizing:border-box;margin:0;padding:0}
html,body{width:1200px;height:4091px;overflow:hidden;background:var(--white)}
body{font-family:var(--body);color:var(--ink)}
.page{position:relative;width:1200px;height:4091px;overflow:hidden}
.abs{position:absolute}
.btn{position:absolute;display:flex;align-items:center;justify-content:center;border-radius:30px;font-family:var(--body);font-weight:500;font-size:15px;text-decoration:none}
.btn-dark{background:var(--brown);color:var(--white)}
.btn-light{background:var(--white);color:var(--ink)}
.heading{font-family:var(--display);font-weight:800;color:var(--ink);letter-spacing:1px}

/* hero */
.hero-photo{left:0;top:0;width:1200px;height:790px;background:linear-gradient(180deg,#3f5f7e 0%,#6f8aa4 28%,#5d6f5a 45%,#33462f 62%,#7a5a3e 85%,#5b4330 100%)}
.hero-curve{left:0;top:560px}
.nav{left:111px;top:75px;width:978px;height:57px;background:var(--white);border-radius:30px;box-shadow:0 2px 10px rgba(0,0,0,.12)}
.nav a{position:absolute;top:0;height:57px;display:flex;align-items:center;font-size:12.5px;color:var(--ink);text-decoration:none}
.nav .active{left:0;width:74px;justify-content:center;background:var(--brown);color:var(--white);font-weight:700;border-radius:30px 0 0 30px}
.nav .book{left:832px;top:9px;height:40px;width:133px;justify-content:center;background:var(--brown);color:var(--white);border-radius:22px;font-size:15px;font-weight:500}
.nav-badge{left:521px;top:28px;width:158px;height:158px;border-radius:50%;background:var(--white);display:flex;align-items:center;justify-content:center;text-align:center;font-family:var(--body);font-weight:500;font-size:14px;line-height:1.25;color:var(--brown);padding:20px}
.hero-title{left:0;top:228px;width:1200px;text-align:center;font-family:var(--display);font-weight:700;font-size:49px;line-height:58px;color:var(--white);text-shadow:0 2px 6px rgba(0,0,0,.3)}

/* domes */
.deco-peaks{border-radius:50% 50% 8px 8px;background:linear-gradient(180deg,rgba(200,200,200,0) 0%,var(--grey-deco) 60%)}
.section-title{left:0;width:1200px;text-align:center;font-size:41px}
.card{width:318px;height:458px;background:var(--white);box-shadow:0 2px 10px rgba(0,0,0,.15);border-radius:4px}
.card.featured{background:var(--brown)}
.card .photo{position:absolute;left:9px;top:9px;width:300px;height:246px;border-radius:6px}
.card h3{position:absolute;left:14px;top:272px;font-family:var(--body);font-weight:400;font-size:25px;color:var(--ink)}
.card.featured h3{color:var(--white);font-weight:500}
.specs{position:absolute;left:20px;top:318px;display:flex;gap:23px;font-size:15px;color:#333}
.card.featured .specs{color:#ddd}
.specs span{display:flex;align-items:flex-end;gap:4px}
.specs svg{width:26px;height:22px}
.card .btn{left:13px;top:379px;width:176px;height:42px}
.card.featured .btn{width:123px}
.arrow{width:16px;height:16px;border-radius:50%;background:#8a8a8a;display:flex;align-items:center;justify-content:center}

/* offers */
.offers-photo{left:0;top:1489px;width:596px;height:601px;background:linear-gradient(160deg,#d9cdb8 0%,#c9b99c 35%,#a47a52 62%,#6b4a32 80%,#3a5a5a 100%)}
.offers-panel{left:596px;top:1489px;width:604px;height:601px;background:var(--panel)}
.offers-title{left:644px;top:1528px;font-size:38px;line-height:51px}
.amenities{left:648px;top:1650px;list-style:none}
.amenities li{display:flex;align-items:center;gap:16px;height:58.5px;font-size:20px;color:var(--ink)}
.amenities .ic{width:44px;height:44px;border-radius:50%;background:#7a7a7a;display:flex;align-items:center;justify-content:center}
.amenities .ic.dark{background:var(--brown)}

/* about */
.about-title{left:110px;top:2168px;font-size:44px}
.about-copy{left:111px;top:2235px;width:450px;font-family:'Arimo',sans-serif;font-size:13.5px;line-height:30px;color:var(--muted)}
.about-mark{left:670px;top:2185px;width:392px;height:300px;border-radius:196px 196px 30px 30px;background:linear-gradient(180deg,#ededed,#bdbdbd);display:flex;align-items:center;justify-content:center;font-family:var(--body);font-weight:500;font-size:26px;color:var(--brown);text-align:center}

/* banner */
.banner{left:111px;top:2597px;width:978px;height:391px;border-radius:22px;background:linear-gradient(180deg,#3b3f66 0%,#262a40 40%,#0b0d12 75%,#050608 100%)}
.banner-title{left:154px;top:2672px;font-family:var(--display);font-weight:700;font-size:41px;line-height:59px;color:var(--white)}

/* gallery */
.gallery-photo{top:3154px;height:402px;border-radius:3px}

/* footer */
.footer{left:0;top:3640px}
.foot-head{font-family:var(--display);font-weight:700;font-size:17px;letter-spacing:2px;color:var(--white)}
.foot-links{list-style:none;left:109px;top:3849px}
.foot-links li{height:28.3px;font-size:13px;color:var(--white)}
.foot-brand{left:420px;top:3908px;width:360px;text-align:center;font-family:var(--body);font-weight:500;font-size:27px;line-height:30px;color:var(--white);letter-spacing:1px}
.foot-circle{left:523px;top:3768px;width:154px;height:128px;border-radius:50%;background:rgba(255,255,255,.92)}
.social{left:513px;top:3998px;display:flex;gap:5px}
.social span{width:30px;height:30px;border-radius:50%;background:var(--white)}
.contact{left:852px;top:3860px;list-style:none}
.contact li{display:flex;align-items:center;gap:16px;height:51px;font-size:13.5px;letter-spacing:1px;color:var(--white)}
.rule{left:108px;top:4056px;width:984px;height:1px;background:rgba(255,255,255,.7)}
.copyright{left:0;top:4062px;width:1200px;text-align:center;font-size:13px;color:var(--white)}
</style>
</head>
<body>
<div class="page">

  <!-- Hero -->
  <div class="abs hero-photo" role="img" aria-label="Photo of a white geodesic dome on a wooden deck with red chairs, forest and a rainbow over the mountains"></div>
  <svg class="abs hero-curve" width="1200" height="240" viewBox="0 0 1200 240" aria-hidden="true">
    <path d="M0 60 Q600 420 1200 60 L1200 240 L0 240 Z" fill="#fff"/>
    <path d="M0 62 Q600 422 1200 62" fill="none" stroke="#3b2920" stroke-width="6"/>
  </svg>

  <nav class="abs nav">
    <a class="active" href="#">Home</a>
    <a href="#" style="left:89px">Accommodations</a>
    <a href="#" style="left:225px">Explore Morvane</a>
    <a href="#" style="left:344px">Contact</a>
    <a href="#" style="left:601px">Why Choose Us</a>
    <a href="#" style="left:727px">Testimonials</a>
    <a class="book" href="#">Book Now</a>
  </nav>
  <div class="abs nav-badge">Tollen Ridge Canvas Camps</div>

  <h1 class="abs hero-title">Your Mountain Escape Near<br>Morvane National Park</h1>
  <a class="btn btn-light" href="#" style="left:482px;top:369px;width:176px;height:41px">Check Availability</a>

  <!-- Our Domes -->
  <div class="abs deco-peaks" style="left:975px;top:775px;width:196px;height:102px" role="img" aria-label="Faint grey mountain peaks decoration"></div>
  <h2 class="abs heading section-title" style="top:858px">Our Domes</h2>

  <div class="abs arrow" style="left:43px;top:1127px"><svg width="8" height="8" viewBox="0 0 8 8"><path d="M5 1 L2 4 L5 7" stroke="#fff" stroke-width="1.6" fill="none"/></svg></div>
  <div class="abs arrow" style="left:1132px;top:1127px;background:#bdbdbd"><svg width="8" height="8" viewBox="0 0 8 8"><path d="M3 1 L6 4 L3 7" stroke="#fff" stroke-width="1.6" fill="none"/></svg></div>

  <svg width="0" height="0" style="position:absolute">
    <defs>
      <g id="i-guests"><circle cx="8" cy="7" r="3.5" fill="none" stroke="currentColor" stroke-width="1.5"/><circle cx="18" cy="7" r="3.5" fill="none" stroke="currentColor" stroke-width="1.5"/><path d="M2 20 Q3 12 8 12 Q13 12 13 20 M13 20 Q14 12 18 12 Q23 12 24 20" fill="none" stroke="currentColor" stroke-width="1.5"/></g>
      <g id="i-bed"><rect x="3" y="4" width="20" height="9" rx="2" fill="none" stroke="currentColor" stroke-width="1.5"/><path d="M2 13 H24 V18 H2 Z M4 18 V21 M22 18 V21" fill="none" stroke="currentColor" stroke-width="1.5"/></g>
      <g id="i-bath"><path d="M5 11 V4 Q5 2 7 2 Q9 2 9 4" fill="none" stroke="currentColor" stroke-width="1.5"/><path d="M2 11 H24 Q23 19 17 19 H9 Q3 19 2 11 Z M6 19 L5 21 M20 19 L21 21" fill="none" stroke="currentColor" stroke-width="1.5"/></g>
      <g id="i-door"><path d="M6 21 V2 H17 V21 M3 21 H22" fill="none" stroke="currentColor" stroke-width="1.5"/><circle cx="14" cy="12" r="1" fill="currentColor"/></g>
    </defs>
  </svg>

  <article class="abs card" style="left:111px;top:943px">
    <div class="photo" role="img" aria-label="Photo of a dome among birch and spruce trees" style="background:linear-gradient(180deg,#c9ccd0 0%,#8e9b88 50%,#6c6a55 80%,#b79a72 100%)"></div>
    <h3>1 Dome</h3>
    <div class="specs"><span><svg viewBox="0 0 26 22"><use href="#i-guests"/></svg>: 4</span><span><svg viewBox="0 0 26 22"><use href="#i-bed"/></svg>: 2</span><span><svg viewBox="0 0 26 22"><use href="#i-bath"/></svg>: 1</span><span><svg viewBox="0 0 26 22"><use href="#i-door"/></svg>: 1</span></div>
    <a class="btn btn-dark" href="#">Check Availability</a>
  </article>

  <article class="abs card featured" style="left:440px;top:943px">
    <div class="photo" role="img" aria-label="Photo of a lit dome at night" style="background:linear-gradient(180deg,#2f3f4b 0%,#44545c 45%,#9b9a93 70%,#1f2a30 100%)"></div>
    <h3>3 Dome</h3>
    <div class="specs"><span><svg viewBox="0 0 26 22"><use href="#i-guests"/></svg>: 4</span><span><svg viewBox="0 0 26 22"><use href="#i-bed"/></svg>: 1</span><span><svg viewBox="0 0 26 22"><use href="#i-bath"/></svg>: 1</span><span><svg viewBox="0 0 26 22"><use href="#i-door"/></svg>: 1</span></div>
    <a class="btn btn-light" href="#">Book Now</a>
  </article>

  <article class="abs card" style="left:768px;top:943px">
    <div class="photo" role="img" aria-label="Photo of a dome deck with red chairs" style="background:linear-gradient(180deg,#5d7a4d 0%,#7f8f6a 40%,#b98a5c 70%,#a66e44 100%)"></div>
    <h3>1 Dome</h3>
    <div class="specs"><span><svg viewBox="0 0 26 22"><use href="#i-guests"/></svg>: 4</span><span><svg viewBox="0 0 26 22"><use href="#i-bed"/></svg>: 2</span><span><svg viewBox="0 0 26 22"><use href="#i-bath"/></svg>: 1</span><span><svg viewBox="0 0 26 22"><use href="#i-door"/></svg>: 1</span></div>
    <a class="btn btn-dark" href="#">Check Availability</a>
  </article>

  <!-- What this place offers -->
  <div class="abs offers-photo" role="img" aria-label="Photo of the dome interior with kitchenette, bed, bench and teal chairs"></div>
  <div class="abs offers-panel"></div>
  <h2 class="abs heading offers-title">What this place<br>offers</h2>
  <ul class="abs amenities">
    <li><span class="ic"><svg width="22" height="18" viewBox="0 0 22 18"><path d="M2 7 Q11 -1 20 7 M5 10 Q11 5 17 10 M8 13 Q11 11 14 13" fill="none" stroke="#fff" stroke-width="1.6"/><circle cx="11" cy="16" r="1.4" fill="#fff"/></svg></span>Wifi</li>
    <li><span class="ic"><svg width="20" height="18" viewBox="0 0 20 18"><rect x="2" y="3" width="16" height="12" rx="2" fill="none" stroke="#fff" stroke-width="1.5"/><circle cx="8" cy="10" r="3" fill="none" stroke="#fff" stroke-width="1.3"/><path d="M13 7 H16 M13 10 H16" stroke="#fff" stroke-width="1.3"/></svg></span>Air conditioning</li>
    <li><span class="ic"><svg width="18" height="18" viewBox="0 0 18 18"><rect x="2" y="2" width="14" height="14" fill="none" stroke="#fff" stroke-width="1.5"/><rect x="5" y="7" width="8" height="9" fill="none" stroke="#fff" stroke-width="1.3"/></svg></span>Indoor fireplace</li>
    <li><span class="ic dark"><svg width="22" height="16" viewBox="0 0 22 16"><rect x="1" y="1" width="20" height="14" rx="2" fill="none" stroke="#fff" stroke-width="1.5"/><rect x="4" y="4" width="10" height="8" fill="none" stroke="#fff" stroke-width="1.3"/><path d="M17 4 V12" stroke="#fff" stroke-width="1.3"/></svg></span>Microwave</li>
    <li><span class="ic"><svg width="22" height="16" viewBox="0 0 22 16"><path d="M2 11 L4 5 H16 L19 11 Z M2 11 V14 H20 V11" fill="none" stroke="#fff" stroke-width="1.5"/><circle cx="6" cy="14" r="1.5" fill="#fff"/><circle cx="16" cy="14" r="1.5" fill="#fff"/></svg></span>Free parking on premises</li>
    <li><span class="ic"><svg width="20" height="18" viewBox="0 0 20 18"><path d="M2 16 H18 M4 16 V8 H16 V16 M4 11 H16 M10 8 V16 M3 8 L10 2 L17 8" fill="none" stroke="#fff" stroke-width="1.4"/></svg></span>Private backyard</li>
  </ul>
  <a class="btn btn-dark" href="#" style="left:646px;top:2016px;width:212px;height:41px">Book an Accommodation</a>

  <!-- About -->
  <h2 class="abs heading about-title">About Us</h2>
  <p class="abs about-copy">Lorem ipsum dolor sit amet, consectetur adipiscing elit, sed do eiusmod tempor incididunt ut labore et dolore magna aliqua. Ut enim ad minim veniam, quis nostrud exercitation ullamco laboris nisi ut aliquip ex ea commodo consequat. Duis aute irure dolor in reprehenderit in voluptate velit esse cillum dolore eu fugiat nulla pariatur. Excepteur sint occaecat cupidatat non proident, sunt in culpa qui officia deserunt mollit anim id est laborum.</p>
  <a class="btn btn-dark" href="#" style="left:111px;top:2458px;width:116px;height:40px">Read More</a>
  <div class="abs about-mark">Tollen Ridge<br>Canvas Camps</div>

  <!-- Banner -->
  <div class="abs banner" role="img" aria-label="Night photo of a glowing dome under the northern lights with a dark tree line"></div>
  <h2 class="abs banner-title">A Cozy Stay on the<br>Edge of Morvane<br>Adventure</h2>
  <a class="btn btn-light" href="#" style="left:156px;top:2872px;width:116px;height:40px">Book Now</a>

  <!-- Gallery -->
  <div class="abs deco-peaks" style="left:0;top:3022px;width:196px;height:102px" role="img" aria-label="Faint grey mountain peaks decoration"></div>
  <h2 class="abs heading section-title" style="top:3062px">Our Gallery</h2>
  <div class="abs gallery-photo" style="left:111px;width:151px;background:linear-gradient(180deg,#3f74c6 0%,#6b98d8 45%,#3e5a4a 62%,#8f9a6a 80%,#b6ad7c 100%)" role="img" aria-label="Photo of blue sky over a valley with distant hills"></div>
  <div class="abs gallery-photo" style="left:286px;width:628px;background:linear-gradient(180deg,#d8cfbd 0%,#b9c6cf 22%,#8ea07a 45%,#7b8c5d 60%,#a98561 78%,#7a5b41 100%)" role="img" aria-label="Photo from inside a dome looking through the window at the valley with two wicker chairs"></div>
  <div class="abs gallery-photo" style="left:933px;width:153px;background:linear-gradient(180deg,#e4eaf0 0%,#9fb0a0 30%,#3b5a36 60%,#54703f 85%,#6f8550 100%)" role="img" aria-label="Photo of tall spruce trees and a lounge chair"></div>

  <!-- Footer -->
  <svg class="abs footer" width="1200" height="451" viewBox="0 0 1200 451" aria-hidden="true">
    <path d="M0 180 Q600 -130 1200 180 L1200 451 L0 451 Z" fill="#3b2920"/>
    <path d="M0 168 Q600 -142 1200 168" fill="none" stroke="#3b2920" stroke-width="4"/>
  </svg>
  <div class="abs deco-peaks" style="left:1050px;top:3655px;width:150px;height:130px;border-radius:50% 50% 0 0" role="img" aria-label="Faint grey pine tree silhouettes decoration"></div>

  <h3 class="abs foot-head" style="left:108px;top:3812px">Quick Links</h3>
  <ul class="abs foot-links">
    <li>Home</li><li>Accommodations</li><li>Explore Morvane</li><li>Why Choose Us</li><li>Testimonials</li><li>Contact</li>
  </ul>

  <div class="abs foot-circle"></div>
  <div class="abs foot-brand">Tollen Ridge<br>Canvas Camps</div>
  <div class="abs social" aria-label="Social links"><span></span><span></span><span></span><span></span><span></span></div>

  <h3 class="abs foot-head" style="left:855px;top:3814px">Contact Info</h3>
  <ul class="abs contact">
    <li><svg width="20" height="22" viewBox="0 0 20 22"><path d="M10 21 Q2 12 2 8 A8 8 0 0 1 18 8 Q18 12 10 21 Z" fill="#fff"/><circle cx="10" cy="8" r="3" fill="#3b2920"/></svg>Tollen Ridge Rd, AB T0E 1N0</li>
    <li><svg width="20" height="20" viewBox="0 0 20 20"><circle cx="10" cy="10" r="10" fill="#fff"/><path d="M6 5 L8 5 L9 8 L8 9 Q9 11 11 12 L12 11 L15 12 L15 14 Q14 15 12 15 Q6 13 5 7 Q5 5 6 5 Z" fill="#3b2920"/></svg>+1 780 555 0142</li>
    <li><svg width="20" height="20" viewBox="0 0 20 20"><circle cx="10" cy="10" r="10" fill="#fff"/><rect x="5" y="6" width="10" height="8" fill="none" stroke="#3b2920" stroke-width="1.4"/><path d="M5 6 L10 10 L15 6" fill="none" stroke="#3b2920" stroke-width="1.4"/></svg>stay@tollenridgecamps.com</li>
  </ul>

  <div class="abs rule"></div>
  <p class="abs copyright">© 2026 Tollen Ridge Canvas Camps.All rights reserved</p>
</div>
</body>
</html>
```